GUARD AGAINST LAWSUITS

I'm virtually ready to launch my site, but I have a number of edits and modifications that need to be implemented. More importantly, I'm always looking to improve my site, particularly now that I am making my proverbial "FIRST IMPRESSION." Thus, I'm willing to see if there is someone who can add creativity and perhaps improve what I already have, particularly on the All Important Front Page.

```html
<!DOCTYPE html>
<html lang="en">
<head>
<meta charset="utf-8">
<title>Guardline Legal — Legal Service Plan for Business Owners</title>
<link href="https://fonts.googleapis.com/css2?family=Lora:wght@400;500&family=Arimo:wght@400;500;700&display=swap" rel="stylesheet">
<style>
:root{
  --navy:#0a2350;
  --navy-deep:#07193d;
  --red:#a4000e;
  --red-btn:#b3050f;
  --white:#ffffff;
  --ink:#333333;
  --muted:#6e6e6e;
}
*{box-sizing:border-box;margin:0;padding:0}
html,body{width:1200px;height:4025px;overflow:hidden}
body{position:relative;background:var(--white);font-family:"Arimo",Arial,sans-serif;color:var(--ink)}
.abs{position:absolute}
.serif{font-family:"Lora",Georgia,serif;font-weight:400}

/* hero */
.hero-photo{left:0;top:0;width:1200px;height:684px;background:linear-gradient(120deg,#2a1d14 0%,#5a4330 40%,#3c2c20 70%,#1a130e 100%)}
.hero-photo::after{content:"";position:absolute;inset:0;background:rgba(10,10,20,.25)}
.brand{left:111px;top:44px;display:flex;align-items:center;gap:10px;color:var(--white);font-size:17px;font-weight:700}
.brand-dot{width:28px;height:28px;border-radius:50%;background:var(--red);border:3px solid var(--white)}
.nav{left:338px;top:36px;display:flex;gap:26px;color:var(--white);font-size:14px;font-weight:700}
.contact-chip{display:flex;gap:12px;color:var(--white);font-size:13px;line-height:21px}
.contact-chip b{font-weight:700}
.chip-icon{width:30px;height:30px;border-radius:50%;background:var(--red);flex:none;display:flex;align-items:center;justify-content:center;margin-top:10px}
.play{left:555px;top:297px;width:90px;height:90px;border-radius:50%;background:var(--red);display:flex;align-items:center;justify-content:center}
.side-photo{left:600px;top:684px;width:600px;height:566px;background:linear-gradient(135deg,#3a2618 0%,#6b4a30 45%,#2b1d14 100%)}
.intro-box{left:111px;top:566px;width:600px;height:562px;background:var(--navy);padding:92px 50px 0 50px;color:var(--white)}
.intro-box h1{font-size:46px;line-height:1;margin-bottom:22px;letter-spacing:.5px}
.intro-box p{font-size:13.4px;line-height:25.8px;text-align:justify}
.intro-box .cta-line{font-weight:700;margin-top:14px}
.btn{display:inline-flex;align-items:center;justify-content:center;background:var(--red-btn);color:var(--white);font-size:13.5px;font-weight:500;height:54px;outline:2px solid var(--white);outline-offset:-5px;box-shadow:0 0 0 1px var(--red-btn)}
.hero-btns{display:flex;gap:20px;margin-top:31px}

/* about */
.about{left:0;top:1250px;width:1200px;height:867px;background:var(--navy);color:var(--white)}
.about h2{position:absolute;left:111px;top:90px;font-size:45px}
.about .lead{position:absolute;left:430px;top:91px;width:659px;font-size:13.2px;line-height:25.8px;text-align:justify}
.about-photo{position:absolute;left:111px;top:228px;width:455px;height:444px;background:linear-gradient(135deg,#8a8060 0%,#c9c2a4 45%,#6f8a6e 75%,#d6a94a 100%)}
.about .story{position:absolute;left:600px;top:218px;width:489px;font-size:13.2px;line-height:25.8px;text-align:justify}
.about .story p+p{margin-top:25.8px}
.about .btn{position:absolute;left:462px;top:711px;width:279px}

/* services */
.services h2{position:absolute;left:111px;top:2225px;font-size:45px;color:var(--navy)}
.services .lead{position:absolute;left:505px;top:2232px;width:584px;font-size:13px;line-height:25.8px;color:var(--muted)}
.card{position:absolute;top:2319px;width:464px;height:445px}
.card-photo{position:absolute;left:0;top:0;width:464px;height:358px}
.card-body{position:absolute;left:74px;top:229px;width:390px;height:216px;background:var(--white);padding:22px 24px 0 24px}
.card-body h3{font-size:22px;font-weight:500;color:#222;margin-bottom:10px;letter-spacing:.3px}
.card-body p{font-size:13px;line-height:21.5px;color:var(--muted);text-align:justify}
.card .btn{position:absolute;left:272px;top:395px;width:167px;height:50px;outline:none;box-shadow:none;font-size:13.5px}
.slider-arrow{position:absolute;left:1126px;width:36px;height:36px;border-radius:50%;background:var(--navy);display:flex;align-items:center;justify-content:center}

/* faq */
.faq{left:0;top:2875px;width:1200px;height:713px;background:var(--red)}
.faq h2{position:absolute;left:0;width:1200px;top:88px;text-align:center;font-size:45px;color:var(--white)}
.faq-item{position:absolute;left:225px;width:750px;height:69px;background:var(--white);display:flex;align-items:center;padding:0 12px 0 31px;justify-content:space-between}
.faq-item span{font-family:"Lora",Georgia,serif;font-size:19px;line-height:26px;color:#333}
.faq-plus{width:45px;height:45px;background:var(--navy);flex:none;display:flex;align-items:center;justify-content:center}

/* footer */
.footer{left:0;top:3588px;width:1200px;height:437px;background:var(--navy);color:var(--white)}
.footer-brand{position:absolute;left:0;width:1200px;top:100px;display:flex;align-items:center;justify-content:center;gap:10px;font-size:20px;font-weight:700}
.footer-nav{position:absolute;left:0;width:1200px;top:208px;display:flex;justify-content:center;gap:34px;font-size:14px}
.footer-card{position:absolute;top:259px;height:81px;width:286px;background:#0f3576;display:flex;align-items:center;gap:18px;padding:0 16px 0 16px;font-size:14px;line-height:21.5px}
.footer-card .chip-icon{width:48px;height:48px;margin:0}
.copyright{position:absolute;left:0;width:1200px;top:380px;text-align:center;font-size:13px}
</style>
</head>
<body>

<!-- hero -->
<div class="abs hero-photo" role="img" aria-label="Courtroom scene with attorney addressing the judge"></div>
<div class="abs brand"><span class="brand-dot"></span>Guardline Legal</div>
<nav class="abs nav"><span>Home</span><span>About</span><span>Contact</span><span>Product</span></nav>
<div class="abs contact-chip" style="left:657px;top:24px">
  <div class="chip-icon"><svg width="14" height="14" viewBox="0 0 24 24"><path fill="#fff" d="M6.6 10.8a15 15 0 0 0 6.6 6.6l2.2-2.2c.3-.3.7-.4 1-.2 1.1.4 2.3.6 3.6.6.6 0 1 .4 1 1V20c0 .6-.4 1-1 1A17 17 0 0 1 3 4c0-.6.4-1 1-1h3.5c.6 0 1 .4 1 1 0 1.3.2 2.5.6 3.6.1.3 0 .7-.2 1z"/></svg></div>
  <div>Call Us :<br><b>555.014.2290</b></div>
</div>
<div class="abs contact-chip" style="left:829px;top:24px">
  <div class="chip-icon"><svg width="14" height="14" viewBox="0 0 24 24"><path fill="#fff" d="M12 2a7 7 0 0 0-7 7c0 5 7 13 7 13s7-8 7-13a7 7 0 0 0-7-7zm0 9.5a2.5 2.5 0 1 1 0-5 2.5 2.5 0 0 1 0 5z"/></svg></div>
  <div>Address :<br><b>4820 Mesa Ridge Rd., Suite 210<br>Tempe, Arizona 85281</b></div>
</div>
<div class="abs play"><svg width="32" height="32" viewBox="0 0 24 24"><path fill="#fff" d="M6 3l15 9-15 9z"/></svg></div>
<div class="abs side-photo" role="img" aria-label="Judge in robe reading papers while on the phone in a library office"></div>
<section class="abs intro-box">
  <h1 class="serif">BUSINESS OWNERS:</h1>
  <p>Guardline Legal (GLP) Is An Extremely Affordable Legal Service Plan (As Little As $8.00 Per Month) That INSULATES Business Owners From Unwarranted LEGAL CLAIMS And Expensive LAWSUITS. Our Plan Uses Local, Experienced, Quality Attorneys Who Focus On PROBLEM PREVENTION Using Proprietary Tools Available Only To GLP Members. Contact Us For A Free Consultation And Receive A FREE OVERVIEW Of Your Business To See If You Are Truly Insulated From Legal Claims.</p>
  <p class="cta-line">Contact us to find out how you can join us to GUARD AGAINST LAWSUITS!!</p>
  <div class="hero-btns">
    <span class="btn" style="width:186px">LEARN MORE</span>
    <span class="btn" style="width:279px">SCHEDULE FREE CONSULATION</span>
  </div>
</section>

<!-- about -->
<section class="abs about">
  <h2 class="serif">ABOUT US</h2>
  <p class="lead">GLP is a group of attorney and legal assistants with many years of experience in litigation, who are devoted to PREVENTING LEGAL CLAIMS and COSTLY LAWSUITS through a variety of FREE and VERY AFFORDABLE services described below. OUR UNIQUE SERVICE PLAN MAKES IT POSSIBLE FOR US TO GUARD AGAINST LAWSUITS.</p>
  <div class="about-photo" role="img" aria-label="Close-up of a hundred dollar bill portrait wearing a face mask"></div>
  <div class="story">
    <p>A homebuilding company was sued by a former employee who claimed to have been promised a more favorable sales area, which claim was disputed by the homebuilder. There was no evidence that such a promise had been made, other than the plaintiff's oral testimony. The company had the case dismissed, but spent $10,000 defending the case.</p>
    <p>And even though it was awarded its attorney's fees, the plaintiff proved uncollectible. Had the company been an GLP member, the case likely would never have been filed. Call for your FREE CONSULTATION and let us show you why the plaintiff likely would not have found a contingency attorney (as was the case) or been able to pay an attorney on an hourly basis. In short, by using GLP's services, the plaintiff's claim would not have been filed.</p>
    <p>In our vast experience with commercial litigation, we believe that a very large percentage of litigation cases hinge on "he said / she said" issues. By using GLP's services, we believe we can INSULATE you and your business from all such issues, which will MINIMIZE your EXPOSURE to LEGAL CLAIMS and LAWSUITS.</p>
  </div>
  <span class="btn">SCHEDULE FREE CONSULATION</span>
</section>

<!-- services -->
<section class="services">
  <h2 class="serif">OUR SERVICES</h2>
  <p class="lead">The price for a membership is a ridiculously low $9.95 PER WEEK. We believe that this fee is very affordable. So what is it? Membership includes the following:</p>
  <article class="card" style="left:111px">
    <div class="card-photo" role="img" aria-label="Attorney gesturing across a desk beside scales of justice" style="background:linear-gradient(135deg,#e9e4dc 0%,#b9a58a 45%,#6a5436 80%,#3b2c1c 100%)"></div>
    <div class="card-body">
      <h3>FREE INITIAL CONSULTATION</h3>
      <p>As a prospective Guardline Legal ("GLP") member, we urge you to schedule an initial consultation with us – at no charge – where we will go over each of the services in detail, and offer an overview of your business formation at no charge.</p>
    </div>
    <span class="btn">LEARN MORE</span>
  </article>
  <article class="card" style="left:625px">
    <div class="card-photo" role="img" aria-label="Brass scales and gavel in front of blurred bookshelves" style="background:linear-gradient(135deg,#c9a27a 0%,#8c5a3a 40%,#a98058 70%,#5a3a28 100%)"></div>
    <div class="card-body">
      <h3>PROPRIETARY CONTRACT</h3>
      <p>GLP members are entitled to incorporate exclusive proprietary contract language in their contracts, work orders, and other written agreements in their business, that MINIMIZES EXPOSURE to legal claims against your business.</p>
    </div>
    <span class="btn">LEARN MORE</span>
  </article>
  <div class="slider-arrow" style="top:2507px"><svg width="16" height="16" viewBox="0 0 24 24"><path fill="none" stroke="#fff" stroke-width="2.4" d="M20 12H5m6-6-6 6 6 6"/></svg></div>
  <div class="slider-arrow" style="top:2550px"><svg width="16" height="16" viewBox="0 0 24 24"><path fill="none" stroke="#fff" stroke-width="2.4" d="M4 12h15m-6-6 6 6-6 6"/></svg></div>
</section>

<!-- faq -->
<section class="abs faq">
  <h2 class="serif">FREQUENTLY ASKED QUESTIONS</h2>
  <div class="faq-item" style="top:181px"><span>Why should I be concerned about legal claims?</span><div class="faq-plus"><svg width="20" height="20" viewBox="0 0 20 20"><path stroke="#fff" stroke-width="2" d="M10 2v16M2 10h16"/></svg></div></div>
  <div class="faq-item" style="top:269px"><span>Provide more details about the value of GLP's contract language.</span><div class="faq-plus"><svg width="20" height="20" viewBox="0 0 20 20"><path stroke="#fff" stroke-width="2" d="M10 2v16M2 10h16"/></svg></div></div>
  <div class="faq-item" style="top:356px"><span>If I'm a contractor, for example, how can an GLP membership<br>minimize legal claims against my business?</span><div class="faq-plus"><svg width="20" height="20" viewBox="0 0 20 20"><path stroke="#fff" stroke-width="2" d="M10 2v16M2 10h16"/></svg></div></div>
  <div class="faq-item" style="top:445px"><span>What does an GLP membership cost?</span><div class="faq-plus"><svg width="20" height="20" viewBox="0 0 20 20"><path stroke="#fff" stroke-width="2" d="M10 2v16M2 10h16"/></svg></div></div>
  <div class="faq-item" style="top:533px"><span>Do you have a Referral Program?</span><div class="faq-plus"><svg width="20" height="20" viewBox="0 0 20 20"><path stroke="#fff" stroke-width="2" d="M10 2v16M2 10h16"/></svg></div></div>
</section>

<!-- footer -->
<footer class="abs footer">
  <div class="footer-brand"><span class="brand-dot"></span>Guardline Legal</div>
  <nav class="footer-nav"><span>Home</span><span>About</span><span>Services</span><span>Faq</span><span>Contact Us</span><span>Terms Of Service</span><span>Privacy Policy</span></nav>
  <div class="footer-card" style="left:300px">
    <div class="chip-icon"><svg width="16" height="16" viewBox="0 0 24 24"><path fill="#fff" d="M12 2a7 7 0 0 0-7 7c0 5 7 13 7 13s7-8 7-13a7 7 0 0 0-7-7zm0 9.5a2.5 2.5 0 1 1 0-5 2.5 2.5 0 0 1 0 5z"/></svg></div>
    <div>4820 Mesa Ridge Rd.,<br>Suite 210 Tempe, Arizona<br>85281</div>
  </div>
  <div class="footer-card" style="left:612px">
    <div class="chip-icon"><svg width="16" height="16" viewBox="0 0 24 24"><path fill="#fff" d="M6.6 10.8a15 15 0 0 0 6.6 6.6l2.2-2.2c.3-.3.7-.4 1-.2 1.1.4 2.3.6 3.6.6.6 0 1 .4 1 1V20c0 .6-.4 1-1 1A17 17 0 0 1 3 4c0-.6.4-1 1-1h3.5c.6 0 1 .4 1 1 0 1.3.2 2.5.6 3.6.1.3 0 .7-.2 1z"/></svg></div>
    <div>Phone :<br>555.014.2290 /<br>800.555.0147</div>
  </div>
  <p class="copyright">Copyright © 2023 | Company name. All rights reserved.</p>
</footer>

</body>
</html>
```